RWT Fittings Ltd Business Cards

We need a business card with our business logo. We provide window and door installations on high-rises in west coast British Colombia, Canada.

I would like my business information and details on one side of the card, and the other side the company name with logo

Target Market(s)

General Contractors

Industry/Entity Type

Construction

Contact Information for Business Card

one side i want my company name and logo in the dark theme logo that i provided

Requirements
Must have
• Marco Peltieri, 16045518293, RWTFittings@mailbox-demo.com, 1407-5194 Linden Row Burnaby BC, V5H 2K9, Owner & Manager

```html
<!DOCTYPE html>
<html lang="en">
<head>
<meta charset="utf-8">
<title>RWT Fittings Ltd – Business Cards</title>
<link rel="stylesheet" href="https://fonts.googleapis.com/css2?family=Montserrat:wght@600;700&family=Roboto:wght@400;500&display=swap">
<style>
  :root {
    --backdrop: #232323;
    --card: #1f2024;
    --card-edge: #29a8e0;
    --accent: #29a8e0;
    --grey: #a9abae;
    --white: #f2f2f2;
  }
  * { box-sizing: border-box; margin: 0; padding: 0; }
  html, body { width: 1200px; height: 780px; overflow: hidden; }
  body {
    background: var(--backdrop);
    position: relative;
    font-family: "Roboto", Arial, sans-serif;
  }
  .card {
    position: absolute;
    width: 560px;
    height: 320px;
    background: var(--card);
    border-radius: 22px;
    border-bottom: 4px solid var(--card-edge);
    border-left: 3px solid var(--card-edge);
    overflow: hidden;
  }
  .card--front { left: 60px; top: 70px; }
  .card--back  { left: 580px; top: 390px; }

  .brand {
    display: flex;
    align-items: center;
    gap: 14px;
    font-family: "Montserrat", Arial, sans-serif;
    font-weight: 700;
    color: var(--accent);
    letter-spacing: 1px;
  }
  .brand__mark { background: var(--accent); flex: none; }

  .card--front .brand {
    position: absolute;
    left: 0; right: 0; top: 0; bottom: 0;
    justify-content: center;
    font-size: 38px;
  }
  .card--front .brand__mark { width: 40px; height: 40px; }

  .card--back .brand {
    position: absolute;
    left: 34px; top: 40px;
    font-size: 24px;
  }
  .card--back .brand__mark { width: 26px; height: 26px; }

  .holder {
    position: absolute;
    right: 46px; top: 112px;
    text-align: right;
  }
  .holder__name {
    font-family: "Montserrat", Arial, sans-serif;
    font-weight: 700;
    font-size: 27px;
    line-height: 1.1;
  }
  .holder__first { color: var(--accent); }
  .holder__last { color: var(--grey); }
  .holder__role {
    font-family: "Montserrat", Arial, sans-serif;
    font-weight: 600;
    font-size: 13px;
    color: var(--white);
    margin-top: 4px;
  }
  .accent-bar {
    position: absolute;
    right: 0; top: 104px;
    width: 18px; height: 62px;
    background: var(--accent);
  }

  .contact {
    position: absolute;
    left: 40px; bottom: 34px;
    color: var(--white);
    font-size: 14px;
    line-height: 1.35;
  }
  .contact__address { margin-bottom: 12px; }
  .contact__row { display: flex; align-items: center; gap: 10px; }
  .contact__row svg { width: 15px; height: 15px; flex: none; }
</style>
</head>
<body>

  <section class="card card--front" aria-label="Card front">
    <div class="brand">
      <span class="brand__mark"></span>
      <span class="brand__name">RWT Fittings Ltd</span>
    </div>
  </section>

  <section class="card card--back" aria-label="Card back">
    <div class="brand">
      <span class="brand__mark"></span>
      <span class="brand__name">RWT Fittings Ltd</span>
    </div>

    <div class="holder">
      <p class="holder__name"><span class="holder__first">Marco</span> <span class="holder__last">Peltieri</span></p>
      <p class="holder__role">Owner &amp; Manager</p>
    </div>
    <span class="accent-bar"></span>

    <div class="contact">
      <p class="contact__address">1407-5194 Linden Row<br>Burnaby BC, V5H 2K9</p>
      <p class="contact__row">
        <svg viewBox="0 0 24 24" aria-hidden="true"><path fill="#29a8e0" d="M6.6 10.8a15.1 15.1 0 0 0 6.6 6.6l2.2-2.2a1 1 0 0 1 1-.25 11.4 11.4 0 0 0 3.6.57 1 1 0 0 1 1 1V20a1 1 0 0 1-1 1A17 17 0 0 1 3 4a1 1 0 0 1 1-1h3.5a1 1 0 0 1 1 1c0 1.25.2 2.45.57 3.57a1 1 0 0 1-.25 1z"/></svg>
        <span>1604 551 8293</span>
      </p>
      <p class="contact__row">
        <svg viewBox="0 0 24 24" aria-hidden="true"><rect x="2" y="5" width="20" height="14" rx="2" fill="none" stroke="#29a8e0" stroke-width="2"/><path d="M3 6l9 7 9-7" fill="none" stroke="#29a8e0" stroke-width="2"/></svg>
        <span>RWTFittings@mailbox-demo.com</span>
      </p>
    </div>
  </section>

</body>
</html>
```